Plumo Ridge - Graphic Label

Company Name: Verdant Loom
Product: Organic Energy Drink
Name of Drink : Plumo Ridge
8.45oz - Bottle
http://www.trellimart.example/item/metal-beverage-flask_2749301856.html?s=p
Attached will be examples of labels for other drinks associated with this company along with company logo. I'm open to all interpretations of design. Please submit creative ideas and we can adjust design as we go.
Design must have some integration of the geometry as seen in labels attached.
Keep it classy
If you have a vision for the design, just create it and we can adjust from there.
I want the bottle to have long lasting but creative/interesting design..
Reason: Design sought has not been submited, the deadline has been extended.
Please continue submissions.
- Thanks
Target Market(s)
All Ages .. those interested in Organics, health drinks, energy drinks
Industry/Entity Type
It Company
Look and feel

```html
<!DOCTYPE html>
<html lang="en">
<head>
<meta charset="utf-8">
<title>Plumo Ridge – Organic Energy Label</title>
<link rel="stylesheet" href="https://fonts.googleapis.com/css2?family=Arvo:wght@700&family=Courgette&family=Lobster+Two:wght@700&display=swap">
<style>
  :root {
    --purple: #5e1a8c;
    --purple-deep: #4a1270;
    --purple-bright: #7a2bb0;
    --leaf-green: #74ab57;
    --white: #ffffff;
    --silver-dark: #8f9296;
    --silver-mid: #c7c9cc;
    --silver-light: #f4f5f6;
    --page: #ffffff;
  }
  * { box-sizing: border-box; margin: 0; padding: 0; }
  html, body {
    width: 1012px;
    height: 1200px;
    overflow: hidden;
    background: var(--page);
  }
  .label {
    position: relative;
    width: 1012px;
    height: 1200px;
    overflow: hidden;
    background: linear-gradient(90deg,
      var(--silver-dark) 0%,
      var(--silver-mid) 14%,
      var(--silver-light) 34%,
      var(--white) 46%,
      var(--silver-mid) 70%,
      var(--silver-light) 82%,
      var(--silver-dark) 100%);
  }
  .geometry {
    position: absolute;
    inset: 0;
  }
  .brand-mark {
    position: absolute;
    top: 178px;
    left: 0;
    width: 100%;
    display: flex;
    justify-content: center;
    align-items: center;
    gap: 12px;
  }
  .brand-mark__dot {
    width: 22px;
    height: 22px;
    border-radius: 50%;
    background: var(--leaf-green);
  }
  .brand-mark__name {
    font-family: "Courgette", cursive;
    font-size: 34px;
    color: var(--white);
  }
  .product-name {
    position: absolute;
    top: 352px;
    left: 0;
    width: 100%;
    text-align: center;
    color: var(--purple);
  }
  .product-name__first {
    display: block;
    font-family: "Lobster Two", cursive;
    font-weight: 700;
    font-size: 170px;
    line-height: 1;
  }
  .product-name__second {
    display: block;
    margin-top: -6px;
    font-family: "Arvo", serif;
    font-weight: 700;
    font-size: 66px;
    letter-spacing: 12px;
    line-height: 1;
  }
  .fruit-art {
    position: absolute;
    top: 600px;
    left: 296px;
    width: 420px;
    height: 230px;
    border-radius: 50%;
    background: radial-gradient(ellipse at 50% 50%,
      #2a1530 0%, #3b1d44 38%, #5e8a3e 72%, rgba(116,171,87,0) 100%);
  }
  .tagline {
    position: absolute;
    top: 842px;
    left: 0;
    width: 100%;
    text-align: center;
    font-family: "Courgette", cursive;
    font-size: 54px;
    color: var(--purple);
  }
  .claims {
    position: absolute;
    top: 928px;
    left: 0;
    width: 100%;
    display: flex;
    justify-content: center;
    gap: 22px;
  }
  .claim {
    width: 130px;
    height: 114px;
  }
  .claim text {
    font-family: "Arvo", serif;
    font-weight: 700;
    font-size: 22px;
    fill: var(--white);
    text-anchor: middle;
  }
</style>
</head>
<body>
<main class="label">
  <svg class="geometry" width="1012" height="1200" viewBox="0 0 1012 1200" aria-hidden="true">
    <polygon points="0,0 1012,0 1012,110 506,330 0,110" fill="var(--purple)"/>
    <polygon points="0,0 1012,0 1012,40 506,40 0,40" fill="var(--purple-deep)"/>
    <polygon points="0,1200 506,1040 1012,1200" fill="var(--purple)"/>
    <circle cx="506" cy="1138" r="40" fill="var(--white)"/>
    <circle cx="506" cy="1138" r="32" fill="none" stroke="var(--purple)" stroke-width="3"/>
  </svg>

  <div class="brand-mark">
    <span class="brand-mark__dot"></span>
    <span class="brand-mark__name">Verdant Loom</span>
  </div>

  <h1 class="product-name">
    <span class="product-name__first">Plumo</span>
    <span class="product-name__second">RIDGE</span>
  </h1>

  <div class="fruit-art" role="img" aria-label="Cluster of dark purple berries with green leaves"></div>

  <p class="tagline">Organic Energy</p>

  <div class="claims">
    <svg class="claim" viewBox="0 0 130 114" aria-label="100% Juice">
      <polygon points="32,2 98,2 128,57 98,112 32,112 2,57" fill="var(--leaf-green)"/>
      <text x="65" y="52">100%</text>
      <text x="65" y="80">Juice</text>
    </svg>
    <svg class="claim" viewBox="0 0 130 114" aria-label="No GMO">
      <polygon points="32,2 98,2 128,57 98,112 32,112 2,57" fill="var(--leaf-green)"/>
      <text x="65" y="52">No</text>
      <text x="65" y="80">GMO</text>
    </svg>
    <svg class="claim" viewBox="0 0 130 114" aria-label="100% Vegan">
      <polygon points="32,2 98,2 128,57 98,112 32,112 2,57" fill="var(--leaf-green)"/>
      <text x="65" y="52">100%</text>
      <text x="65" y="80">Vegan</text>
    </svg>
  </div>
</main>
</body>
</html>
```